We are a recruitment company based in Norwich/Cambridge England.
I have included our company logo which we want to remain the same.

What we are looking for is a new creative Business card which will really stand out!!

Contact Information for Business Card

Harriet Dunmore
email: Harriet@plavex.co.uk
Address: Brackwell House
Fenmoor Enterprise Park
Partridge Way
Norwich
QB9 3KX
Tel:01632 960418

```html
<!DOCTYPE html>
<html lang="en">
<head>
<meta charset="utf-8">
<title>Plavex – Business Card</title>
<link rel="stylesheet" href="https://fonts.googleapis.com/css2?family=Montserrat:wght@400;500;600;700&display=swap">
<style>
  :root {
    --backdrop: #17181a;
    --card: #25282a;
    --card-edge: #2c2f31;
    --green: #7dc242;
    --grey: #a7a6aa;
    --grey-soft: #8d8e90;
    --white: #e9e9ea;
  }
  * { margin: 0; padding: 0; box-sizing: border-box; }
  html, body {
    width: 1200px;
    height: 800px;
    overflow: hidden;
    background: var(--backdrop);
    font-family: "Montserrat", Arial, sans-serif;
  }
  .canvas {
    position: relative;
    width: 1200px;
    height: 800px;
  }
  .card {
    position: absolute;
    width: 540px;
    height: 310px;
    background: var(--card);
    border: 1px solid var(--card-edge);
    border-radius: 4px;
    overflow: hidden;
    box-shadow: 0 18px 40px rgba(0,0,0,.55);
  }
  .card--front { left: 50px; top: 110px; }
  .card--back  { left: 610px; top: 380px; }

  /* brand lockup */
  .brand {
    display: flex;
    align-items: center;
    gap: 12px;
  }
  .brand__dot {
    width: 34px;
    height: 34px;
    border-radius: 50%;
    background: var(--green);
    flex: none;
  }
  .brand__name {
    font-weight: 700;
    color: var(--green);
    letter-spacing: -0.5px;
    line-height: 1;
  }
  .brand__tagline {
    font-size: 8px;
    font-weight: 500;
    letter-spacing: 2.6px;
    color: var(--grey);
    margin-top: 4px;
  }

  /* front side */
  .card--front .brand-block {
    position: absolute;
    left: 50%;
    top: 96px;
    transform: translateX(-50%);
    display: flex;
    flex-direction: column;
    align-items: center;
  }
  .card--front .brand__dot { width: 48px; height: 48px; }
  .card--front .brand__name { font-size: 52px; }
  .card--front .brand__tagline { text-align: right; align-self: flex-end; }
  .website {
    margin-top: 22px;
    font-size: 12px;
    letter-spacing: 3px;
    color: var(--grey);
  }
  .website__domain { color: var(--green); }

  /* back side */
  .card--back .brand-block {
    position: absolute;
    right: 34px;
    top: 34px;
    display: flex;
    flex-direction: column;
    align-items: flex-end;
  }
  .card--back .brand__dot { width: 32px; height: 32px; }
  .card--back .brand__name { font-size: 34px; }
  .card--back .brand__tagline { font-size: 6px; letter-spacing: 2px; }

  .side-marker {
    position: absolute;
    left: -22px;
    top: 98px;
    width: 44px;
    height: 44px;
    border-radius: 50%;
    background: var(--green);
  }
  .person {
    position: absolute;
    left: 40px;
    top: 96px;
  }
  .person__name {
    font-size: 21px;
    font-weight: 700;
    color: var(--green);
    line-height: 1.1;
  }
  .person__role {
    font-size: 14px;
    font-weight: 400;
    color: var(--grey);
    letter-spacing: 1px;
  }

  .contact-list {
    position: absolute;
    left: 34px;
    bottom: 30px;
    list-style: none;
  }
  .contact-list__item {
    display: flex;
    align-items: center;
    gap: 10px;
    font-size: 12px;
    color: var(--grey);
    line-height: 1;
    margin-top: 8px;
  }
  .contact-list__icon {
    width: 18px;
    height: 18px;
    flex: none;
  }

  .address {
    position: absolute;
    right: 34px;
    bottom: 30px;
    text-align: right;
    font-style: normal;
    font-size: 11.5px;
    line-height: 1.5;
    color: var(--grey);
  }
</style>
</head>
<body>
<main class="canvas">

  <section class="card card--front" aria-label="Business card front">
    <div class="brand-block">
      <div class="brand">
        <span class="brand__dot"></span>
        <span class="brand__name">Plavex</span>
      </div>
      <p class="brand__tagline">Technology Recruitment</p>
      <p class="website">www.<span class="website__domain">plavex</span>.co.uk</p>
    </div>
  </section>

  <section class="card card--back" aria-label="Business card back">
    <div class="brand-block">
      <div class="brand">
        <span class="brand__dot"></span>
        <span class="brand__name">Plavex</span>
      </div>
      <p class="brand__tagline">Technology Recruitment</p>
    </div>

    <span class="side-marker"></span>
    <div class="person">
      <p class="person__name">Harriet Dunmore</p>
      <p class="person__role">CEO</p>
    </div>

    <ul class="contact-list">
      <li class="contact-list__item">
        <svg class="contact-list__icon" viewBox="0 0 18 18" aria-hidden="true">
          <circle cx="9" cy="9" r="8" fill="none" stroke="#7dc242" stroke-width="1.4"/>
          <rect x="6.2" y="4.2" width="5.6" height="9.6" rx="1" fill="none" stroke="#7dc242" stroke-width="1.2"/>
          <line x1="8.2" y1="12" x2="9.8" y2="12" stroke="#7dc242" stroke-width="1"/>
        </svg>
        01632 960418
      </li>
      <li class="contact-list__item">
        <svg class="contact-list__icon" viewBox="0 0 18 18" aria-hidden="true">
          <circle cx="9" cy="9" r="8" fill="#7dc242"/>
          <rect x="4.8" y="6" width="8.4" height="6" fill="none" stroke="#25282a" stroke-width="1.1"/>
          <polyline points="4.8,6 9,9.4 13.2,6" fill="none" stroke="#25282a" stroke-width="1.1"/>
        </svg>
        Harriet@plavex.co.uk
      </li>
      <li class="contact-list__item">
        <svg class="contact-list__icon" viewBox="0 0 18 18" aria-hidden="true">
          <circle cx="9" cy="9" r="8" fill="#7dc242"/>
          <circle cx="9" cy="9" r="4.4" fill="none" stroke="#25282a" stroke-width="1"/>
          <ellipse cx="9" cy="9" rx="1.9" ry="4.4" fill="none" stroke="#25282a" stroke-width="0.9"/>
          <line x1="4.6" y1="9" x2="13.4" y2="9" stroke="#25282a" stroke-width="0.9"/>
        </svg>
        www.plavex.co.uk
      </li>
    </ul>

    <address class="address">
      Brackwell House<br>
      Fenmoor Enterprise Park<br>
      Partridge Way<br>
      Norwich QB9 3KX
    </address>
  </section>

</main>
</body>
</html>
```